- Redesign our business card
- Logo remains unchanged
- Current business card attached

Target Market(s)

We are a property management company

Industry/Entity Type

Business

```html
<!DOCTYPE html>
<html lang="en">
<head>
<meta charset="utf-8">
<title>Harcourt Property Group – Business Card</title>
<link rel="stylesheet" href="https://fonts.googleapis.com/css2?family=Barlow:wght@400;500;600&display=swap">
<style>
  :root {
    --backdrop: #1f2117;
    --card-white: #ffffff;
    --olive: #6b7340;
    --stone: #d3c89d;
    --slate: #5f5a5a;
    --ink: #2e2e2e;
    --font: "Barlow", Arial, sans-serif;
  }
  * { margin: 0; padding: 0; box-sizing: border-box; }
  html, body {
    width: 1198px; height: 1200px; overflow: hidden;
    background: var(--backdrop);
    font-family: var(--font);
  }
  .canvas { position: relative; width: 1198px; height: 1200px; }

  .card { position: absolute; border-radius: 33px; overflow: hidden; }
  .card-front { left: 72px; top: 142px; width: 794px; height: 442px; background: var(--card-white); }
  .card-back { left: 332px; top: 616px; width: 792px; height: 440px; background: var(--stone); }

  .abs { position: absolute; white-space: nowrap; line-height: 1; }

  .holder-name { left: 361px; top: 91px; font-size: 24px; font-weight: 600; color: var(--ink); }
  .holder-title { left: 361px; top: 120px; font-size: 18px; font-weight: 400; color: var(--ink); }
  .address { left: 361px; top: 208px; font-size: 18.5px; color: var(--ink); line-height: 26px; }

  .contacts { left: 361px; top: 273px; list-style: none; }
  .contacts li { display: flex; align-items: center; height: 26px; font-size: 18.5px; color: var(--ink); }
  .contact-key {
    width: 15px; height: 15px; margin-right: 22px; background: var(--olive);
    color: #fff; font-size: 10px; font-weight: 600; display: flex;
    align-items: flex-end; justify-content: flex-end; padding: 0 2px 1px 0;
  }

  .front-brand { left: 30px; top: 300px; display: flex; align-items: center; gap: 12px;
    font-size: 22px; font-weight: 600; color: var(--olive); }
  .brand-square { width: 18px; height: 18px; background: var(--olive); }

  .service-band { position: absolute; left: 0; bottom: 0; width: 100%; height: 49px; background: var(--olive);
    color: #fff; font-size: 19px; font-weight: 600; padding-left: 72px; display: flex; align-items: center; }
  .service-band .sep { margin: 0 10px; }

  .back-brand { left: 387px; top: 276px; display: flex; align-items: center; gap: 12px;
    font-size: 22px; font-weight: 600; color: var(--olive); letter-spacing: 0.5px; }
  .back-tagline { left: 387px; top: 303px; font-size: 16px; color: var(--slate); letter-spacing: 0.6px; }
  .back-web { left: 387px; top: 368px; font-size: 22px; font-weight: 600; color: var(--olive); }
</style>
</head>
<body>
<main class="canvas">
  <section class="card card-front" aria-label="Business card front">
    <p class="abs holder-name">Daniel Harcourt</p>
    <p class="abs holder-title">Licensed Strata Manager</p>
    <p class="abs address">PO Box 48, Elmwood Park NSW 2031<br>12/5-19 Calder Lane Redfield NSW 2016</p>
    <ul class="abs contacts">
      <li><span class="contact-key">T</span>02 9555 0148</li>
      <li><span class="contact-key">F</span>02 9555 0172</li>
      <li><span class="contact-key">M</span>0400 555 219</li>
      <li><span class="contact-key">E</span>info@harcourtproperty.com.au</li>
    </ul>
    <p class="abs front-brand"><span class="brand-square"></span>Harcourt Property Group</p>
    <p class="service-band">Strata Management<span class="sep">|</span>Community Management<span class="sep">|</span>Property Management</p>
  </section>

  <section class="card card-back" aria-label="Business card back">
    <p class="abs back-brand"><span class="brand-square"></span>HARCOURT PROPERTY GROUP</p>
    <p class="abs back-tagline">STRATA MANAGEMENT SERVICES</p>
    <p class="abs back-web">www.harcourtproperty.com.au</p>
  </section>
</main>
</body>
</html>
```